Public Speaking Book for aspiring, ambitious speakers

I'm looking for a 6x9 book cover (Brivora standard) as well as ebook and audiobook formats.

I'm looking for orange font on a white background as these are my brand colours.

Feel free to use some yellow and gold too if you deem it appropriate.

Title: Climb and Kindle
Subtitle: Find Your Voice. Tell Your Story. Share your Message.
Author: Owen Thistlewood

I would like to have a picture of a female speaker on the front cover.

Alternatively, some kind of image that symbolises public speaking like a microphone, podium etc

Target Market(s)

Aspiring professional speakers

Colors
f78f20

Requirements
Must have
• Correct spelling!
Nice to have
• A logo or picture that fits the theme, but no pressure if you can't think of anything
Should not have
• No men in suits please. I don't want this to have a 1980s corporate look.

```html
<!DOCTYPE html>
<html lang="en">
<head>
<meta charset="UTF-8">
<title>Climb and Kindle — Book Cover</title>
<link rel="stylesheet" href="https://fonts.googleapis.com/css2?family=Bebas+Neue&family=Poppins:wght@400;600&display=swap">
<style>
  :root {
    --brand-orange: #f78f20;
    --stage: #e8871f;
    --cover-dark: #131316;
    --sky-light: #f1eff5;
    --haze: #e9d9c8;
    --sun-gold: #e8a15a;
    --earth: #4a3322;
    --text-light: #d6d6d6;
    --text-ink: #1b1b1b;
  }
  html, body {
    margin: 0;
    padding: 0;
    width: 1200px;
    height: 1200px;
    overflow: hidden;
    background: var(--stage);
  }
  .canvas {
    position: relative;
    width: 1200px;
    height: 1200px;
  }
  .book-cover {
    position: absolute;
    left: 214px;
    top: 20px;
    width: 772px;
    height: 1160px;
    background: var(--cover-dark);
    overflow: hidden;
  }
  .cover-photo {
    position: absolute;
    left: 0;
    top: 0;
    width: 100%;
    height: 640px;
    background:
      radial-gradient(ellipse 120px 140px at 50% 36%, rgba(255,214,150,0.95), rgba(255,214,150,0) 70%),
      linear-gradient(to bottom,
        var(--sky-light) 0%,
        var(--sky-light) 34%,
        var(--haze) 48%,
        var(--sun-gold) 62%,
        #8a5a35 76%,
        var(--earth) 86%,
        var(--cover-dark) 100%);
  }
  .author-name {
    position: absolute;
    top: 48px;
    left: 0;
    width: 100%;
    margin: 0;
    text-align: center;
    font-family: 'Poppins', sans-serif;
    font-weight: 400;
    font-size: 27px;
    letter-spacing: 1.5px;
    color: var(--text-ink);
  }
  .book-title {
    position: absolute;
    top: 600px;
    left: 0;
    width: 100%;
    margin: 0;
    text-align: center;
    font-family: 'Bebas Neue', sans-serif;
    font-weight: 400;
    font-size: 186px;
    line-height: 0.84;
    color: var(--brand-orange);
  }
  .book-title .title-accent {
    color: var(--text-light);
  }
  .book-subtitle {
    position: absolute;
    top: 935px;
    left: 0;
    width: 100%;
    margin: 0;
    text-align: center;
    font-family: 'Poppins', sans-serif;
    font-weight: 600;
    font-size: 34px;
    line-height: 1.36;
    color: var(--text-light);
  }
</style>
</head>
<body>
  <main class="canvas">
    <section class="book-cover">
      <div class="cover-photo" role="img" aria-label="Photograph of a group of friends seen from behind, arms around each other, facing a hazy golden sunset over hills — a symbol of rising together and speaking out"></div>
      <p class="author-name">OWEN THISTLEWOOD</p>
      <h1 class="book-title">Climb <span class="title-accent">and</span><br>Kindle</h1>
      <p class="book-subtitle">Find Your Voice.<br>Tell Your Story.<br>Share your Message.</p>
    </section>
  </main>
</body>
</html>
```